Corvane Capital Business Cards

These are professional business cards that are for my family office.
Put fake emails and phone numbers as of now until I finalize those components. This family office controls my families investments, assets, and future. The cards should be professional.
..
.
.
.
I just uploaded another variation of a logo I would like to see as a business card to I am inbeteen which logo to use

Target Market(s)

business

Industry/Entity Type

business

Contact Information for Business Card

Professional, wealth related, finance related.

Requirements
Must have
• Logo

```html
<!DOCTYPE html>
<html lang="en">
<head>
<meta charset="utf-8">
<title>Corvane Capital Business Cards</title>
<link rel="stylesheet" href="https://fonts.googleapis.com/css2?family=Cinzel:wght@600&family=Montserrat:wght@400;700&display=swap">
<style>
  :root {
    --bg: #2a2a2c;
    --navy: #1c2033;
    --card-white: #ffffff;
    --card-grey: #a7a7a7;
    --band-grey: #a9a9a9;
    --text: #1c2033;
    --muted: #3a3d4a;
  }
  * { margin: 0; padding: 0; box-sizing: border-box; }
  html, body { width: 1200px; height: 874px; overflow: hidden; background: var(--bg); }
  .canvas { position: relative; width: 1200px; height: 874px; }
  .card {
    position: absolute; left: 280px; width: 640px; height: 366px;
    border-radius: 22px; overflow: hidden;
    box-shadow: 0 10px 24px rgba(0,0,0,.45);
  }
  .card--front { top: 50px; background: var(--card-grey); }
  .card--back { top: 458px; background: var(--card-white); }

  .brand { position: absolute; display: flex; flex-direction: column; align-items: center; }
  .brand__circle { border: 3px solid var(--navy); border-radius: 50%; }
  .brand__name {
    font-family: 'Cinzel', serif; font-weight: 600; color: var(--navy);
    letter-spacing: .02em; white-space: nowrap;
  }
  .card--front .brand { left: 0; right: 0; top: 70px; }
  .card--front .brand__circle { width: 150px; height: 150px; }
  .card--front .brand__name { font-size: 38px; margin-top: 22px; }

  .card--back .brand { left: 20px; width: 300px; top: 58px; }
  .card--back .brand__circle { width: 120px; height: 120px; border-width: 2.5px; }
  .card--back .brand__name { font-size: 27px; margin-top: 14px; }

  .divider { position: absolute; left: 340px; top: 46px; width: 2px; height: 226px; background: var(--navy); }

  .details { position: absolute; left: 368px; top: 50px; font-family: 'Montserrat', sans-serif; color: var(--text); }
  .details__name { font-weight: 700; font-size: 24px; line-height: 1.1; }
  .details__title { font-size: 13px; color: var(--muted); margin-top: 2px; }
  .details__address { font-size: 14px; line-height: 1.3; margin-top: 18px; }
  .contact { list-style: none; margin-top: 12px; }
  .contact li { display: flex; align-items: center; gap: 9px; font-size: 14.5px; line-height: 1.75; }
  .contact svg { width: 13px; height: 13px; fill: var(--navy); flex: none; }

  .band { position: absolute; top: 296px; height: 28px; }
  .band--navy { left: 0; width: 480px; background: var(--navy); }
  .band--grey { left: 480px; right: 0; background: var(--band-grey); }
  .band__badge {
    position: absolute; left: 460px; top: 290px; width: 40px; height: 40px;
    border-radius: 50%; background: var(--card-white); border: 2px solid var(--navy);
  }
</style>
</head>
<body>
<main class="canvas">
  <section class="card card--front" aria-label="Card front">
    <div class="brand">
      <div class="brand__circle"></div>
      <p class="brand__name">Corvane Capital</p>
    </div>
  </section>

  <section class="card card--back" aria-label="Card back">
    <div class="brand">
      <div class="brand__circle"></div>
      <p class="brand__name">Corvane Capital</p>
    </div>
    <div class="divider"></div>
    <div class="details">
      <p class="details__name">Marcus Ellery</p>
      <p class="details__title">Owner</p>
      <p class="details__address">48 Linden Court<br>Ashbury, NJ 07012 USA</p>
      <ul class="contact">
        <li><svg viewBox="0 0 24 24"><path d="M6.6 10.8a15.1 15.1 0 0 0 6.6 6.6l2.2-2.2c.3-.3.7-.4 1-.2 1.1.4 2.3.6 3.6.6.6 0 1 .4 1 1V20c0 .6-.4 1-1 1A17 17 0 0 1 3 4c0-.6.4-1 1-1h3.5c.6 0 1 .4 1 1 0 1.3.2 2.5.6 3.6.1.3 0 .7-.2 1z"/></svg>(555)214-7730</li>
        <li><svg viewBox="0 0 24 24"><path d="M2 5h20v14H2z M2 5l10 8 10-8" /></svg>info@corvanecapital.com</li>
        <li><svg viewBox="0 0 24 24"><path d="M12 2a10 10 0 1 0 0 20 10 10 0 0 0 0-20zm0 2c1 1.2 1.8 3 2 5h-4c.2-2 1-3.8 2-5zm-2.6.4C8.6 6 8.1 7.4 8 9H4.6a8 8 0 0 1 4.8-4.6zM4.6 15H8c.1 1.6.6 3 1.4 4.6A8 8 0 0 1 4.6 15zM10 15h4c-.2 2-1 3.8-2 5-1-1.2-1.8-3-2-5zm4.6 4.6c.8-1.6 1.3-3 1.4-4.6h3.4a8 8 0 0 1-4.8 4.6zM16 9c-.1-1.6-.6-3-1.4-4.6A8 8 0 0 1 19.4 9zM4.2 11H8v2H4.2a8 8 0 0 1 0-2zm5.8 0h4v2h-4zm6 0h3.8a8 8 0 0 1 0 2H16z"/></svg>www.corvanecapital.com</li>
      </ul>
    </div>
    <div class="band band--navy"></div>
    <div class="band band--grey"></div>
    <div class="band__badge"></div>
  </section>
</main>
</body>
</html>
```